Computer Repair Business - Needs New Business Card Design

I want to create a very cool business card for my business. I want to make it 100% different from my previous card. I would like to use similar color scheme like Royal blue.

With this card I want to create a conversation and have my customers say "Wow, that's a cool business card" Trying to prevent it from looking like the typical card that get's shoved into a wallet.

My website is below:

www.lornapcfix.com

I want to edit the hours and website and email:

www.lornapcfix.com
lorna@lornapcfix.com

10:30 to 6pm Monday - Friday
10:30 to 3pm Saturday
Updates

Just to remind, when i see a new design i don't want to notice my old design.

Business card will be printed and made with rounded corners and horizontal.

The back of the card should say " In-Store Repair, Remote Support, Data Recovery"

Industry/Entity Type

Business

Font styles to use
Sans Serif

Colors
33a6d7
3176b5

Requirements
Must have
• Clean looking - have creative aspects.
Should not have
• Should not look like the previous card design.

```html
<!DOCTYPE html>
<html lang="en">
<head>
<meta charset="utf-8">
<title>Lorna PC Fix – Business Card</title>
<link href="https://fonts.googleapis.com/css2?family=Open+Sans:wght@400;700&family=Roboto+Condensed:wght@400&display=swap" rel="stylesheet">
<style>
  :root {
    --royal: #1d5cb4;
    --royal-dark: #174c96;
    --ink: #1a1a1a;
    --paper: #ffffff;
    --paper-shade: #e9e9e9;
    --stage: #d9d9d9;
    --icon-tone: #dfe6f2;
  }
  * { margin: 0; padding: 0; box-sizing: border-box; }
  html, body { width: 1200px; height: 800px; overflow: hidden; }
  body {
    background: var(--stage);
    font-family: "Open Sans", Arial, sans-serif;
    position: relative;
  }
  .card {
    position: absolute;
    top: 245px;
    width: 540px;
    height: 309px;
    border-radius: 14px;
    overflow: hidden;
    box-shadow: 0 6px 18px rgba(0,0,0,0.18);
  }
  .card-front { left: 40px; background: var(--royal); }
  .card-back { left: 620px; background: var(--royal); }

  .front-shape { position: absolute; inset: 0; }

  .holder { position: absolute; left: 30px; top: 26px; color: var(--paper); }
  .holder-name { font-weight: 700; font-size: 17px; letter-spacing: 0.3px; }
  .holder-role { font-size: 12px; margin-top: 1px; }

  .address { position: absolute; left: 30px; top: 100px; color: var(--paper); font-size: 12px; line-height: 1.6; font-style: normal; }

  .contacts { position: absolute; left: 30px; top: 198px; list-style: none; color: var(--paper); font-size: 11px; }
  .contacts li { display: flex; align-items: center; gap: 8px; height: 19px; }
  .contacts svg { width: 11px; height: 11px; flex: none; }

  .brand {
    position: absolute; left: 332px; top: 138px;
    display: flex; align-items: center; gap: 8px;
    white-space: nowrap;
  }
  .brand-mark { width: 18px; height: 18px; background: var(--royal); flex: none; }
  .brand-name { font-weight: 700; font-size: 21px; color: var(--ink); letter-spacing: 0.3px; }

  .services {
    position: absolute; top: 42px; left: 0; right: 0;
    display: flex; justify-content: center; gap: 60px;
    font-family: "Roboto Condensed", "Arial Narrow", sans-serif;
    color: var(--paper);
  }
  .service { width: 110px; display: flex; flex-direction: column; align-items: center; text-align: center; }
  .service-art { width: 70px; height: 70px; background: var(--icon-tone); border-radius: 6px; margin-bottom: 14px; }
  .service-label { font-size: 16px; line-height: 1.2; }

  .hours {
    position: absolute; left: 0; right: 0; bottom: 36px;
    text-align: center;
    font-family: "Roboto Condensed", "Arial Narrow", sans-serif;
    color: var(--paper);
  }
  .hours-main { font-size: 13px; }
  .hours-note { font-size: 12px; margin-top: 4px; }
</style>
</head>
<body>

<section class="card card-front" aria-label="Card front">
  <svg class="front-shape" viewBox="0 0 540 309" preserveAspectRatio="none" aria-hidden="true">
    <defs>
      <linearGradient id="paperFade" x1="0" y1="0" x2="1" y2="1">
        <stop offset="0" stop-color="#e9e9e9"/>
        <stop offset="0.5" stop-color="#ffffff"/>
      </linearGradient>
    </defs>
    <path d="M318,0 C232,70 222,220 282,309 L306,309 C250,220 262,80 352,0 Z" fill="#1a1a1a"/>
    <path d="M352,0 C262,80 250,220 306,309 L540,309 L540,0 Z" fill="url(#paperFade)"/>
  </svg>

  <div class="holder">
    <p class="holder-name">MARK JENSEN</p>
    <p class="holder-role">Managing Director</p>
  </div>

  <address class="address">
    215 Oak Ridge Rd,<br>Millbrook, NJ 07999
  </address>

  <ul class="contacts">
    <li>
      <svg viewBox="0 0 12 12"><path d="M2.5 1 L4.5 1 L5.3 3.4 L4 4.4 C4.7 6 6 7.3 7.6 8 L8.6 6.7 L11 7.5 L11 9.5 C11 10.3 10.3 11 9.5 11 C5 11 1 7 1 2.5 C1 1.7 1.7 1 2.5 1 Z" fill="#ffffff"/></svg>
      <span>908 555 0142</span>
    </li>
    <li>
      <svg viewBox="0 0 12 12"><rect x="0.5" y="2" width="11" height="8" rx="1" fill="#ffffff"/><path d="M1 2.5 L6 6.5 L11 2.5" stroke="#1d5cb4" fill="none" stroke-width="1"/></svg>
      <span>lorna@lornapcfix.com</span>
    </li>
    <li>
      <svg viewBox="0 0 12 12"><circle cx="6" cy="6" r="5" fill="none" stroke="#ffffff" stroke-width="1.2"/><ellipse cx="6" cy="6" rx="2.2" ry="5" fill="none" stroke="#ffffff" stroke-width="1"/><line x1="1" y1="6" x2="11" y2="6" stroke="#ffffff" stroke-width="1"/></svg>
      <span>www.lornapcfix.com</span>
    </li>
  </ul>

  <div class="brand">
    <span class="brand-mark"></span>
    <span class="brand-name">LORNA PC FIX</span>
  </div>
</section>

<section class="card card-back" aria-label="Card back">
  <div class="services">
    <div class="service">
      <div class="service-art" role="img" aria-label="Screwdriver illustration"></div>
      <p class="service-label">In-Store<br>Repair</p>
    </div>
    <div class="service">
      <div class="service-art" role="img" aria-label="Globe with network illustration"></div>
      <p class="service-label">Remote<br>Support</p>
    </div>
    <div class="service">
      <div class="service-art" role="img" aria-label="Computer chip illustration"></div>
      <p class="service-label">Data<br>Recovery</p>
    </div>
  </div>

  <div class="hours">
    <p class="hours-main">Hours / MON - FRI 10:30 am - 6:00 pm / SAT 10:30 am - 3:00 pm</p>
    <p class="hours-note">After hours support available by appointment</p>
  </div>
</section>

</body>
</html>
```